wealth management firm, professional group, new model

we have a logo that works but we need a card, white background using our colors...clean look

our tag line if can be used in

The Path From Saver to Steward

```html
<!DOCTYPE html>
<html lang="en">
<head>
<meta charset="utf-8">
<title>Arcova Capital Advisors – Business Card</title>
<link rel="stylesheet" href="https://fonts.googleapis.com/css2?family=Montserrat:wght@400;500;700;800&display=swap">
<style>
  :root {
    --navy: #172d52;
    --navy-deep: #142a4d;
    --silver: #c9ccd1;
    --grey-swoosh: #a3a5a8;
    --paper: #ffffff;
    --ink: #1b1b1f;
    --backdrop: #e4e5e7;
  }
  * { box-sizing: border-box; margin: 0; padding: 0; }
  html, body { width: 1200px; height: 856px; overflow: hidden; }
  body {
    background: var(--backdrop);
    font-family: "Montserrat", Arial, sans-serif;
    display: flex;
    align-items: center;
    justify-content: center;
    gap: 36px;
  }
  .card {
    position: relative;
    width: 560px;
    height: 320px;
    overflow: hidden;
    box-shadow: 0 14px 30px rgba(0,0,0,.25);
  }
  .card--front { background: var(--paper); }
  .card--back {
    background: var(--navy-deep);
    display: flex;
    align-items: center;
    justify-content: center;
  }
  .card__swoosh { position: absolute; inset: 0; width: 100%; height: 100%; }

  .brand {
    color: var(--navy);
    font-weight: 400;
    text-align: center;
    line-height: 1;
  }
  .brand__name { display: block; }
  .brand__sub { display: block; }
  .brand--front { position: absolute; left: 34px; top: 108px; width: 220px; }
  .brand--front .brand__name { font-size: 34px; letter-spacing: 11px; margin-right: -11px; }
  .brand--front .brand__sub { font-size: 10.5px; letter-spacing: 4px; margin-top: 12px; margin-right: -4px; }
  .brand--back { color: var(--silver); }
  .brand--back .brand__name { font-size: 58px; letter-spacing: 22px; margin-right: -22px; }
  .brand--back .brand__sub { font-size: 18px; letter-spacing: 7px; margin-top: 20px; margin-right: -7px; }

  .divider {
    position: absolute;
    left: 272px; top: 52px;
    width: 1.5px; height: 150px;
    background: var(--navy);
  }
  .contact { position: absolute; left: 288px; top: 48px; color: var(--ink); }
  .contact__name { color: var(--navy); font-weight: 800; font-size: 19px; letter-spacing: .3px; }
  .contact__title { font-size: 12px; margin-top: 3px; }
  .contact__tagline { font-size: 12px; margin-top: 10px; }
  .contact__list { list-style: none; margin-top: 8px; }
  .contact__item { display: flex; align-items: center; gap: 8px; font-size: 12px; margin-top: 5px; }
  .contact__icon { width: 12px; height: 12px; flex: none; }
</style>
</head>
<body>
  <section class="card card--front" aria-label="Card front">
    <svg class="card__swoosh" viewBox="0 0 560 320" preserveAspectRatio="none" aria-hidden="true">
      <path d="M240 320 C400 260 515 160 538 0 L560 0 L560 320 Z" fill="var(--grey-swoosh)"/>
      <path d="M248 320 C405 262 522 165 548 0 L560 0 L560 320 Z" fill="var(--paper)"/>
      <path d="M255 320 C410 265 530 170 560 18 L560 320 Z" fill="var(--navy)"/>
    </svg>

    <div class="brand brand--front">
      <span class="brand__name">ARCOVA</span>
      <span class="brand__sub">CAPITAL ADVISORS</span>
    </div>

    <div class="divider"></div>

    <div class="contact">
      <p class="contact__name">DANIEL MERROW</p>
      <p class="contact__title">Managing Director</p>
      <p class="contact__tagline">The Path From Saver to Steward</p>
      <ul class="contact__list">
        <li class="contact__item">
          <svg class="contact__icon" viewBox="0 0 12 12" aria-hidden="true"><rect x="2.5" y="0.8" width="7" height="10.4" rx="1.4" fill="none" stroke="var(--navy)" stroke-width="1.2"/><circle cx="6" cy="9.3" r=".7" fill="var(--navy)"/></svg>
          555-014-2298
        </li>
        <li class="contact__item">
          <svg class="contact__icon" viewBox="0 0 12 12" aria-hidden="true"><rect x="0.5" y="2.5" width="11" height="7.5" fill="var(--navy)"/><path d="M0.8 2.8 L6 7 L11.2 2.8" fill="none" stroke="#fff" stroke-width="1"/></svg>
          hello@arcovacapital.com
        </li>
        <li class="contact__item">
          <svg class="contact__icon" viewBox="0 0 12 12" aria-hidden="true"><circle cx="6" cy="6" r="5.3" fill="var(--navy)"/><path d="M0.8 6 H11.2 M6 0.8 C3.5 3.5 3.5 8.5 6 11.2 M6 0.8 C8.5 3.5 8.5 8.5 6 11.2" fill="none" stroke="#fff" stroke-width=".7"/></svg>
          www.arcovacapital.com
        </li>
      </ul>
    </div>
  </section>

  <section class="card card--back" aria-label="Card back">
    <div class="brand brand--back">
      <span class="brand__name">ARCOVA</span>
      <span class="brand__sub">CAPITAL ADVISORS</span>
    </div>
  </section>
</body>
</html>
```